New Fun, Positive, energised looking Business Card Needed for High Achiever Coach

I am looking for a two sided full colour business card. I am self employed and have recently re branded my 1-2-1 work re-vitalising high achievers. My target client base for these cards is therefore high achievers - usually aged 40 -55, they are often entrepreneurs, CEO or work in banking and finance and 2/3 are male. I work with them on 90 day or 6 month coaching programs to help them live their success in a healthier, more sustainable and fulfiiled way. They pay for this privately so though they are corporate types the cards need not look 'corporate'. I want to portray the idea of transformation, vitality and re-connecting.
You can get a feel for the look I like on my new website: morvenlisk.co.uk
I want to use this logo with strapline (Re-Vitalising High Achievers) (I purchased off Logoharbor) and font/ colours (the turquoise and green).
Details to include on the card:
www.morvenlisk.co.uk
+44 7915 302618
morven@morvenlisk.co.uk
skype: morvenlisk
I'd also like to include:
Do you struggle to switch off? Want to be healthier and feel fitter? Want closer relationships? More clarity over the direction you are headed? I can help you do these things using integrated mind-body techniques. Visit morvenlisk.co.uk TODAY to apply for a FREE Breakthrough session.
BUT if that is too much text for a card I am open to advice/ammendments.
Updates
Thanks for your design - I am considering them. PLease change the wording to :

```html
<!DOCTYPE html>
<html lang="en">
<head>
<meta charset="utf-8">
<title>Morven Lisk – Business Card</title>
<link href="https://fonts.googleapis.com/css2?family=Alfa+Slab+One&family=Dancing+Script:wght@500&family=Open+Sans:wght@400;600;700&display=swap" rel="stylesheet">
<style>
  :root {
    --stage: #6b6a6e;
    --paper: #ffffff;
    --green: #5cb85f;
    --green-soft: #86c77f;
    --turquoise: #0aa3c9;
    --teal-name: #0e9fc4;
    --lime-link: #b9dd8c;
    --white: #ffffff;
  }
  * { box-sizing: border-box; margin: 0; padding: 0; }
  html, body {
    width: 1007px; height: 1200px; overflow: hidden;
    background: var(--stage);
    font-family: "Open Sans", Arial, sans-serif;
  }
  .canvas { position: relative; width: 1007px; height: 1200px; }

  /* Front of card */
  .card-front {
    position: absolute; left: 60px; top: 67px;
    width: 917px; height: 528px;
    background: var(--paper);
  }
  .band-top {
    position: absolute; left: 0; top: 0; width: 100%; height: 30px;
    background: var(--green);
    border-top-right-radius: 26px;
  }
  .band-bottom {
    position: absolute; left: 0; bottom: 0; width: 100%; height: 30px;
    background: var(--green);
    border-top-left-radius: 26px;
  }
  .front-mark {
    position: absolute; left: 147px; top: 96px;
    width: 150px; height: 150px; border-radius: 50%;
    background: var(--green);
  }
  .front-name {
    position: absolute; left: 28px; top: 326px;
    font-family: "Alfa Slab One", Georgia, serif;
    font-size: 48px; line-height: 1; color: var(--teal-name);
    letter-spacing: 1px;
  }
  .front-tagline {
    position: absolute; left: 30px; top: 386px;
    font-family: "Dancing Script", cursive;
    font-weight: 500;
    font-size: 30px; line-height: 1; color: var(--teal-name);
  }
  .contact-list {
    position: absolute; left: 574px; top: 340px;
    list-style: none;
  }
  .contact-list li {
    display: flex; align-items: center; gap: 8px;
    height: 33.5px;
    font-size: 24px; color: var(--green-soft);
  }
  .contact-list svg { width: 24px; height: 24px; flex: none; }

  /* Back of card */
  .card-back {
    position: absolute; left: 51px; top: 639px;
    width: 917px; height: 525px;
    background: var(--turquoise);
    color: var(--white);
    text-align: center;
  }
  .back-mark {
    position: absolute; left: 421px; top: 127px;
    width: 80px; height: 80px; border-radius: 50%;
    background: var(--white);
  }
  .back-name {
    position: absolute; left: 0; right: 0; top: 268px;
    font-family: "Alfa Slab One", Georgia, serif;
    font-size: 30px; line-height: 1;
  }
  .back-tagline {
    position: absolute; left: 0; right: 0; top: 306px;
    font-family: "Dancing Script", cursive;
    font-weight: 500;
    font-size: 19px; line-height: 1;
  }
  .back-pitch {
    position: absolute; left: 20px; right: 20px; top: 348px;
    font-size: 22px; line-height: 30px;
  }
  .back-pitch .site { color: var(--lime-link); font-weight: 700; }
</style>
</head>
<body>
<main class="canvas">
  <section class="card-front">
    <div class="band-top"></div>
    <div class="front-mark" aria-hidden="true"></div>
    <div class="front-name">Morven Lisk</div>
    <div class="front-tagline">Restoring Energy to Busy Leaders</div>
    <ul class="contact-list">
      <li>
        <svg viewBox="0 0 24 24" aria-hidden="true"><path fill="currentColor" d="M3 9c0-3 4-5 9-5s9 2 9 5l-1 2-4-1v-2c-2-1-6-1-8 0v2l-4 1zM7 13h10l2 7H5z"/></svg>
        +44 7915 302618
      </li>
      <li>
        <svg viewBox="0 0 24 24" aria-hidden="true"><circle cx="12" cy="12" r="10" fill="currentColor"/></svg>
        morvenlisk
      </li>
      <li>
        <svg viewBox="0 0 24 24" aria-hidden="true" fill="none" stroke="currentColor" stroke-width="2"><circle cx="12" cy="12" r="9"/><ellipse cx="12" cy="12" rx="4" ry="9"/><path d="M3 12h18"/></svg>
        www.morvenlisk.co.uk
      </li>
      <li>
        <svg viewBox="0 0 24 24" aria-hidden="true"><rect x="2" y="5" width="20" height="14" fill="currentColor"/><path d="M2 5l10 8 10-8" fill="none" stroke="#fff" stroke-width="1.6"/></svg>
        morven@morvenlisk.co.uk
      </li>
    </ul>
    <div class="band-bottom"></div>
  </section>

  <section class="card-back">
    <div class="back-mark" aria-hidden="true"></div>
    <div class="back-name">Morven Lisk</div>
    <div class="back-tagline">Restoring Energy to Busy Leaders</div>
    <p class="back-pitch">
      Is your mind always racing? Longing for more energy and a stronger body? Want<br>
      deeper connections? A clearer sense of where your life is going? Together we can<br>
      get you there with a blend of practical mind and body coaching.<br>
      Visit <span class="site">morvenlisk.co.uk</span><br>
      NOW to reserve your FREE Discovery conversation.
    </p>
  </section>
</main>
</body>
</html>
```